Hula-Hoop dance entertainment sales and instruction by spin-wavelet needs a business card

I need a 2 sided business card that is square (although this is not an absolute )for my self employed business as an independent artist. my business name is "Spin-Wavelet" I teach how to hula-hoop classes, make and sell hula-hoops, provided entertainment at kids birthday parties, community events, corporate events and perform at artistic dance shows.
I would like to see spirals or curved lines in the card, and I would like the card to be seen as fun, spunky, flair and eye catching.

the card could double as a tag to go on the hoops i sell,

Target Market(s)

women age 20 - 50

Industry/Entity Type

Entertainment

Requirements
Must have
• Dorine Vantash
www.spinwavelet.example
555.014.7263
Nice to have
• I would like my image to be on one side of the card. so people can recognize me!

```html
<!DOCTYPE html>
<html lang="en">
<head>
<meta charset="utf-8">
<title>Dorine Vantash — Spin-Wavelet Business Card</title>
<link rel="stylesheet" href="https://fonts.googleapis.com/css2?family=Grand+Hotel&family=PT+Sans:wght@400;700&display=swap">
<style>
  :root {
    --card-bg: #9ea3d5;
    --ink: #000000;
    --page-bg: #ffffff;
  }
  html, body {
    margin: 0;
    padding: 0;
    width: 1200px;
    height: 1200px;
    overflow: hidden;
    background: var(--page-bg);
  }
  .card {
    position: relative;
    width: 1200px;
    height: 1200px;
    box-sizing: border-box;
    background: var(--card-bg);
    border: 11px solid var(--ink);
    color: var(--ink);
    text-align: center;
  }
  .card__name {
    position: absolute;
    left: 0;
    right: 0;
    top: 18px;
    margin: 0;
    font-family: "Grand Hotel", cursive;
    font-weight: 400;
    font-size: 178px;
    line-height: 220px;
    letter-spacing: 1px;
  }
  .card__rule {
    position: absolute;
    left: 144px;
    width: 890px;
    height: 4px;
    background: var(--ink);
  }
  .card__rule--top { top: 250px; }
  .card__rule--bottom { top: 918px; }
  .services {
    position: absolute;
    left: 0;
    right: 0;
    top: 286px;
    margin: 0;
    padding: 0;
    list-style: none;
    font-family: "PT Sans", sans-serif;
    font-weight: 400;
    font-size: 49px;
    line-height: 66px;
  }
  .contact {
    position: absolute;
    left: 0;
    right: 0;
    top: 962px;
    font-family: "PT Sans", sans-serif;
    font-weight: 700;
    font-size: 62px;
    line-height: 77px;
    letter-spacing: 1px;
  }
  .contact__line { display: block; }
</style>
</head>
<body>
  <main class="card">
    <h1 class="card__name">Dorine Vantash</h1>
    <div class="card__rule card__rule--top"></div>
    <ul class="services">
      <li>Hoop Classes</li>
      <li>Hoop Jams</li>
      <li>Private Lessons</li>
      <li>Custom hula-hoops for adults and kids</li>
      <li>Performances</li>
      <li>Hoop Making Workshops</li>
      <li>Birthday Parties</li>
      <li>Corporate Event Entertainment</li>
      <li>and more!</li>
    </ul>
    <div class="card__rule card__rule--bottom"></div>
    <address class="contact" style="font-style: normal;">
      <span class="contact__line contact__web">www.spinwavelet.example</span>
      <span class="contact__line contact__phone">555.014.7263</span>
    </address>
  </main>
</body>
</html>
```